Business card design Needed for new logo / Construction business, home extensions and new builds

We need a business card design using our new logo files which i will attach to this project :)

We are a small construction business specialising in home extensions, new builds and property development. We are very ambitious and would appreciate professional and elegant designs for our new business card.

Very serious about using the services on MakerQuarry and recently acquired our new logo from here :)

Please get involved, i will feedback when i can as i am very busy but can respond daily, thanks

Target Market(s)

People that want to build onto their houses, new building developments or adding too their existing property

Industry/Entity Type

Construction

Contact Information for Business Card

Renwick Tolliver Construction, Lionel Ashby (Managing Director), Tel 07822254961, email - info@renwick-tolliver, www.renwick-tolliver.co.uk

Colors

Designer to choose colors to be used in the design.

Requirements
Must have
• I like a deep grey on the back please. A lot of you have provided black from and back, try mixing things up a little. The black looks cool 😎 Thanks

```html
<!DOCTYPE html>
<html lang="en">
<head>
<meta charset="utf-8">
<title>Renwick Tolliver Construction – Business Card</title>
<link rel="stylesheet" href="https://fonts.googleapis.com/css2?family=Cinzel:wght@500&family=Poppins:wght@400&display=swap">
<style>
  :root {
    --page: #3a3a3a;
    --card: #171717;
    --card-edge: #0e0e0e;
    --emboss-light: #242424;
    --emboss-dark: #0c0c0c;
    --gold: #d8a632;
    --silver: #cfcfcf;
    --text: #e6e6e6;
  }
  * { margin: 0; padding: 0; box-sizing: border-box; }
  html, body {
    width: 1200px; height: 959px; overflow: hidden;
    background: var(--page);
  }
  .canvas {
    position: relative; width: 1200px; height: 959px;
  }
  .card {
    position: absolute; left: 270px; width: 660px; height: 400px;
    background: var(--card);
    box-shadow: 0 12px 30px rgba(0,0,0,.45);
    overflow: hidden;
  }
  .card--back { top: 48px; }
  .card--front { top: 508px; }

  .emboss-area {
    position: absolute;
    width: 330px; height: 330px;
    border-radius: 4px;
    background: linear-gradient(150deg, var(--emboss-light) 0%, #191919 55%, var(--emboss-dark) 100%);
    opacity: .85;
  }
  .card--back .emboss-area { left: 40px; top: 40px; }
  .card--front .emboss-area { right: 40px; top: 40px; }

  .brand {
    position: absolute;
    display: flex; align-items: center; gap: 14px;
  }
  .brand__square {
    width: 22px; height: 22px; background: var(--gold); flex: none;
  }
  .brand__name {
    font-family: "Cinzel", serif; font-weight: 500;
    color: var(--silver); line-height: 1.25; letter-spacing: .04em;
  }
  .card--back .brand { right: 48px; top: 150px; }
  .card--back .brand__name { font-size: 22px; }
  .card--front .brand { left: 44px; top: 52px; }
  .card--front .brand__name { font-size: 24px; }

  .rule {
    position: absolute; height: 2px; background: var(--gold);
  }
  .card--back .rule { right: 48px; top: 232px; width: 230px; }
  .card--front .rule { left: 44px; top: 140px; width: 250px; }

  .person {
    position: absolute; left: 44px; top: 178px;
  }
  .person__name {
    font-family: "Cinzel", serif; font-weight: 500; font-size: 24px;
    color: var(--silver); letter-spacing: .04em;
  }
  .person__role {
    font-family: "Poppins", sans-serif; font-size: 15px; color: var(--gold);
    margin-top: 2px;
  }
  .contacts {
    position: absolute; left: 44px; top: 262px; list-style: none;
    font-family: "Poppins", sans-serif; font-size: 15px; color: var(--text);
  }
  .contacts li {
    display: flex; align-items: center; gap: 12px; height: 30px;
  }
  .contacts svg { width: 16px; height: 16px; flex: none; }
</style>
</head>
<body>
<main class="canvas">

  <section class="card card--back" aria-label="Card back">
    <div class="emboss-area" role="img" aria-label="Large embossed brand mark"></div>
    <div class="brand">
      <span class="brand__square"></span>
      <span class="brand__name">Renwick Tolliver<br>Construction</span>
    </div>
    <div class="rule"></div>
  </section>

  <section class="card card--front" aria-label="Card front">
    <div class="emboss-area" role="img" aria-label="Large embossed brand mark"></div>
    <div class="brand">
      <span class="brand__square"></span>
      <span class="brand__name">Renwick Tolliver<br>Construction</span>
    </div>
    <div class="rule"></div>

    <div class="person">
      <p class="person__name">Lionel Ashby</p>
      <p class="person__role">Managing Director</p>
    </div>

    <ul class="contacts">
      <li>
        <svg viewBox="0 0 16 16" aria-hidden="true"><path d="M3.5 1.5l2.5 0 1 3.5-1.8 1.2c.8 1.8 2.2 3.2 4 4l1.2-1.8 3.5 1v2.5c0 .8-.7 1.5-1.5 1.5C6.8 13.4 2.6 9.2 2 3c0-.8.7-1.5 1.5-1.5z" fill="var(--gold)"/></svg>
        <span>07822254961</span>
      </li>
      <li>
        <svg viewBox="0 0 16 16" aria-hidden="true"><rect x="1.5" y="3.5" width="13" height="9" fill="none" stroke="var(--gold)" stroke-width="1.4"/><path d="M1.5 3.5L8 9l6.5-5.5" fill="none" stroke="var(--gold)" stroke-width="1.4"/></svg>
        <span>info@renwick-tolliver</span>
      </li>
      <li>
        <svg viewBox="0 0 16 16" aria-hidden="true"><g fill="none" stroke="var(--gold)" stroke-width="1.2"><circle cx="8" cy="8" r="6.3"/><ellipse cx="8" cy="8" rx="2.8" ry="6.3"/><path d="M1.7 8h12.6M2.8 4.8h10.4M2.8 11.2h10.4"/></g></svg>
        <span>www.renwick-tolliver.co.uk</span>
      </li>
    </ul>
  </section>

</main>
</body>
</html>
```